Design a box that holds medical gloves for paramedics!

We need a design for a box of gloves (nitrile gloves). We are designing this for a specific customer whose name is Borvik (their logo is attached as image000.1png). We have also attached the current design for the box which we want to change to be specific for Borvik. Everywhere you see a turtle, replace it with the Borvik logo. There should be no turtles on the box. The people who use these gloves are paramedics who work in an ambulance. The box should look TOUGH, American, and instill confidence and safety. An American flag alone or one incorporating the eagle from the company logo covering the top of the box (perhaps in the background on the top) would be a nice touch. Do not change anything on the bottom of the box, which is the side with the size chart on it. You can change background color but all the info on the bottom of the box needs to stay there. What you send back should be the box with all sides designed. We need to start showing our customer options right away for this box so please don't hesitate to start. We look forward to working with you.
Updates

The Client has changed his mind regarding the use of an American Flag. This product will be sold world wide, so NO FLAGS AT ALL. We still want the box to look TOUGH. We would like the top of the box to have the Borvik Logo very LARGE. We would like the Falcon from the logo to be incorporated somehow into the background of the box. So the whole Falcon or wings of the Borvik faded in background might be nice. The color scheme should still be black, red and white. The design should be bold and tough looking. This initial box will be used for black gloves but in the future the box may have blue gloves so we need some part/aspect of the box to be able to change color to blue or white if we change the color of gloves in the box in the future to have blue or white gloves. Please leave bottom of the box as is shown in original photo uploaded. Thanks and sorry for the change this late in the process.

Target Market(s)

The buyer of this product is a Paramedic who works on an ambulance. Medical market. EMS market.

Industry/Entity Type

Medical

Font styles to use
Sans Serif

Colors
ec1f27
ffffff
1b1b1b

Requirements
Must have
• American Flag
• Patriotic
• Borvik Logo in several places
• Look tough
• Color scheme should be Black, Red and White.

```html
<!DOCTYPE html>
<html lang="en">
<head>
<meta charset="utf-8">
<title>Borvik Nitrile Glove Box – Flat Panels</title>
<link rel="stylesheet" href="https://fonts.googleapis.com/css2?family=PT+Sans:ital,wght@0,400;0,700;1,400&display=swap">
<style>
  :root {
    --stage: #e1e2cc;
    --panel-grey: #8b8b8d;
    --panel-black: #1b1b1b;
    --brand-red: #ec1f27;
    --ink: #111111;
    --white: #ffffff;
    --wing-light: #3a3a3a;
    --wing-dark: #222222;
  }
  * { box-sizing: border-box; margin: 0; padding: 0; }
  html, body { width: 1200px; height: 870px; overflow: hidden; }
  body {
    background: var(--stage);
    font-family: "PT Sans", Arial, sans-serif;
    color: var(--ink);
    position: relative;
  }
  .panel { position: absolute; display: flex; overflow: hidden; }
  .panel-grey { background: var(--panel-grey); position: relative; }
  .panel-black { background: var(--panel-black); position: relative; color: var(--white); }

  /* Top lid */
  .lid { left: 50px; top: 50px; width: 900px; height: 400px; }
  .lid .panel-grey { width: 640px; }
  .lid .panel-black { width: 260px; }

  /* Front side */
  .front { left: 50px; top: 470px; width: 900px; height: 170px; }
  .front .panel-grey { width: 640px; }
  .front .panel-black { width: 260px; }

  /* End flap */
  .end { left: 970px; top: 50px; width: 180px; height: 400px; flex-direction: column; }
  .end .panel-grey { height: 230px; }
  .end .panel-black { height: 170px; }

  .brand-square {
    position: absolute; background: var(--brand-red);
    border-radius: 6px;
  }
  .brand-name {
    position: absolute; font-weight: 700; color: var(--ink);
    letter-spacing: 1px; line-height: 1;
  }
  .rule { position: absolute; height: 2px; background: var(--brand-red); }
  .product-line { position: absolute; font-weight: 700; color: var(--ink); }
  .count-line { position: absolute; font-size: 13px; color: var(--ink); }
  .tagline { position: absolute; font-size: 11px; color: #2a2a2a; }

  .wing-fade {
    position: absolute;
    background: radial-gradient(ellipse at 60% 40%, var(--wing-light) 0%, var(--wing-dark) 55%, var(--panel-black) 80%);
  }

  .features { position: absolute; list-style: none; text-align: right; font-size: 14px; line-height: 1.2; color: var(--white); }
  .features li::after {
    content: ""; display: inline-block; width: 5px; height: 5px;
    background: var(--brand-red); margin-left: 6px; vertical-align: middle;
  }
  .size-badge {
    position: absolute; background: var(--brand-red); color: var(--white);
    font-weight: 700; display: flex; align-items: center; justify-content: center;
    border-radius: 3px;
  }
  .size-word { position: absolute; color: var(--white); font-size: 14px; font-weight: 700; }
  .single-use { position: absolute; color: var(--white); font-size: 13px; font-weight: 700; }
</style>
</head>
<body>

<!-- Top lid -->
<section class="panel lid" aria-label="Box top">
  <div class="panel-grey">
    <div class="brand-square" style="left:40px; top:40px; width:160px; height:120px;"></div>
    <div class="rule" style="left:250px; top:58px; width:330px;"></div>
    <div class="brand-name" style="left:250px; top:72px; font-size:84px;">Borvik</div>
    <div class="rule" style="left:250px; top:168px; width:330px;"></div>
    <div class="product-line" style="left:40px; top:205px; font-size:20px;">Nitrile Powder Free Black Examination Gloves</div>
    <div class="count-line" style="left:40px; top:232px;">100 Gloves by Weight</div>
  </div>
  <div class="panel-black">
    <div class="wing-fade" role="img" aria-label="Faded falcon wing background graphic" style="left:0; top:0; width:260px; height:230px;"></div>
    <ul class="features" style="right:110px; top:160px;">
      <li>Textured</li><li>Non-Sterile</li><li>Ambidextrous</li><li>Latex Free</li>
    </ul>
    <div class="size-badge" style="right:30px; top:150px; width:64px; height:60px; font-size:40px;">L</div>
    <div class="size-word" style="right:40px; top:214px;">Large</div>
    <ul class="features" style="right:30px; top:250px;">
      <li>Textured</li><li>Non-Sterile</li><li>Ambidextrous</li><li>Latex Free</li>
    </ul>
    <div class="single-use" style="right:30px; top:360px;">For Single Use</div>
  </div>
</section>

<!-- Front side -->
<section class="panel front" aria-label="Box front side">
  <div class="panel-grey">
    <div class="brand-square" style="left:30px; top:25px; width:100px; height:76px;"></div>
    <div class="rule" style="left:170px; top:22px; width:260px;"></div>
    <div class="brand-name" style="left:170px; top:32px; font-size:58px;">Borvik</div>
    <div class="rule" style="left:170px; top:100px; width:260px;"></div>
    <div class="product-line" style="left:30px; top:116px; font-size:16px;">Nitrile Powder Free Black Examination Gloves</div>
    <div class="tagline" style="left:30px; top:140px;">Powder free disposable examination gloves made of soft nitrile material</div>
  </div>
  <div class="panel-black">
    <div class="wing-fade" role="img" aria-label="Faded falcon wing background graphic" style="left:0; top:0; width:260px; height:170px;"></div>
    <div class="size-badge" style="left:30px; top:30px; width:50px; height:46px; font-size:30px;">L</div>
    <div class="size-word" style="left:34px; top:80px;">Large</div>
    <ul class="features" style="right:25px; top:22px; font-size:13px;">
      <li>Textured</li><li>Non-Sterile</li><li>Ambidextrous</li><li>Latex Free</li>
    </ul>
    <div class="single-use" style="right:25px; top:130px;">For Single Use</div>
  </div>
</section>

<!-- End flap -->
<section class="panel end" aria-label="Box end">
  <div class="panel-grey">
    <div class="brand-square" style="left:40px; top:24px; width:100px; height:76px;"></div>
    <div class="rule" style="left:20px; top:118px; width:140px;"></div>
    <div class="brand-name" style="left:20px; top:128px; font-size:44px;">Borvik</div>
    <div class="rule" style="left:20px; top:180px; width:140px;"></div>
    <div class="count-line" style="left:20px; top:196px; font-size:12px;">100 Gloves by Weight</div>
  </div>
  <div class="panel-black">
    <ul class="features" style="left:20px; top:22px; font-size:13px; text-align:left;">
      <li>Textured</li><li>Non-Sterile</li><li>Ambidextrous</li><li>Latex Free</li>
    </ul>
    <div class="size-badge" style="right:20px; top:100px; width:50px; height:46px; font-size:30px;">L</div>
    <div class="size-word" style="right:24px; top:148px;">Large</div>
  </div>
</section>

</body>
</html>
```